20 year old business card needs re-design

We need to redesign our corporate business card look. We need something that appears more modern, eye catchy but professional.

Target Market(s)

manufacturing industry

Industry/Entity Type

Manufacturer

Contact Information for Business Card

One side can have the logo. Other side can have contact information.

Font styles to use
Serif

Colors
3277b5
33b8a4
ffffff

Requirements
Must have
• Eye catchy - need to standout from the crowd. company logo cannot change. Full name, job title, phone number and email address.
Should not have
• Fax, business address is not necessary.

```html
<!DOCTYPE html>
<html lang="en">
<head>
<meta charset="utf-8">
<title>Veralon Global – Business Card</title>
<link href="https://fonts.googleapis.com/css2?family=Open+Sans:wght@400;600;700;800&display=swap" rel="stylesheet">
<style>
  :root {
    --backdrop: #3a3330;
    --card: #0d0d0e;
    --ink: #f2f2f2;
    --ink-soft: #d8d8d8;
    --accent: #2f62b8;
  }
  * { box-sizing: border-box; margin: 0; padding: 0; }
  html, body { width: 1200px; height: 844px; overflow: hidden; }
  body {
    background: var(--backdrop);
    font-family: "Open Sans", Arial, sans-serif;
    color: var(--ink);
    position: relative;
  }
  .card {
    position: absolute;
    top: 268px;
    width: 540px;
    height: 308px;
    background: var(--card);
    box-shadow: 0 10px 30px rgba(0,0,0,.45);
  }
  .card--contact { left: 40px; }
  .card--brand { left: 620px; }

  .brand {
    display: flex;
    align-items: center;
    gap: 12px;
  }
  .brand__mark {
    width: 22px; height: 22px;
    background: var(--accent);
  }
  .brand__name {
    font-weight: 800;
    font-size: 42px;
    letter-spacing: -1px;
    color: var(--ink);
    line-height: 1;
  }

  .card--contact .brand { position: absolute; left: 60px; top: 52px; }

  .contact-list {
    position: absolute;
    right: 30px;
    top: 130px;
    list-style: none;
    text-align: right;
    font-size: 13.5px;
    line-height: 22px;
    color: var(--ink-soft);
  }
  .contact-list li { display: flex; justify-content: flex-end; align-items: center; gap: 8px; }
  .contact-list svg { width: 11px; height: 11px; fill: var(--accent); flex: none; }
  .contact-list .certs { margin-top: 10px; padding-right: 19px; }

  .person { position: absolute; left: 40px; top: 212px; }
  .person__name { color: var(--accent); font-weight: 700; font-size: 17px; line-height: 20px; }
  .person__role { font-size: 13.5px; color: var(--ink-soft); line-height: 18px; }
  .person__label { margin-top: 12px; color: var(--accent); font-weight: 600; font-size: 14px; line-height: 18px; }
  .person__sites { font-size: 14px; color: var(--ink-soft); line-height: 18px; }

  .card--brand .brand {
    position: absolute; left: 0; right: 0; top: 106px; justify-content: center;
  }
  .card--brand .brand__name { font-size: 48px; }
  .tagline {
    position: absolute; left: 0; right: 0; top: 196px;
    text-align: center;
    font-weight: 700;
    font-size: 13px;
    line-height: 19px;
    color: var(--ink);
  }
</style>
</head>
<body>
  <section class="card card--contact" aria-label="Contact side">
    <div class="brand">
      <span class="brand__mark"></span>
      <span class="brand__name">Veralon Global</span>
    </div>

    <ul class="contact-list">
      <li>555-014-2200 xt 201
        <svg viewBox="0 0 12 12" aria-hidden="true"><path d="M2.5 1l2 2.2-1.1 1.3a7 7 0 0 0 4.1 4.1l1.3-1.1 2.2 2-1.4 1.5C5.3 10.5 1.5 6.7 1 2.4z"/></svg>
      </li>
      <li>555-014-2281
        <svg viewBox="0 0 12 12" aria-hidden="true"><rect x="3" y="1" width="6" height="3"/><rect x="1" y="4.5" width="10" height="5" rx="1"/><rect x="3" y="8" width="6" height="3"/></svg>
      </li>
      <li>dan@veralonglobal.com
        <svg viewBox="0 0 12 12" aria-hidden="true"><path d="M1 2.5h10v7H1z M1 2.5l5 4 5-4" /></svg>
      </li>
      <li>VeralonGlobal.com
        <svg viewBox="0 0 12 12" aria-hidden="true"><circle cx="6" cy="6" r="5"/></svg>
      </li>
      <li class="certs">TS16949 &amp; ISO9001 Certified Facilities</li>
    </ul>

    <div class="person">
      <p class="person__name">Dan Morell</p>
      <p class="person__role">Senior Project Manager</p>
      <p class="person__label">Offices &amp; Warehousing:</p>
      <p class="person__sites">USA - Taiwan - Mexico</p>
    </div>
  </section>

  <section class="card card--brand" aria-label="Logo side">
    <div class="brand">
      <span class="brand__mark"></span>
      <span class="brand__name">Veralon Global</span>
    </div>
    <p class="tagline">International manufacturing solutions<br>for OEM customers in North America</p>
  </section>
</body>
</html>
```